Business Card Design Project : Ridgeline Press

In preparation for market launch, Tamarind's Ridgeline Press require the development of a business card. Ridgeline Press is a Community online publishing web portal. We provide the the city of Whistler located in B.C. (Canada) business directories, News, Classified ads, News, Events and blogs etc.

The main focus of the brand is to help local businesses to corporate with their online advertisement and marketing. Meeting our clients face to face is a must (B2B).

Target Market(s)

The target market is B2B customers. Business Owners to Marketing, advertising Managers

Industry/Entity Type

Business

Requirements
Must have
• - The business card will be two sided.
the BACK side will have our logo which consist of (icon, url,slogan) submited. The logo will be middle and centred.

The FRONT side should have company details:

Company Legal Name: TAMARIND RIDGELINE MEDIA

Owen Farsk
Director of Sales & Marketing

www.tamarindridgeline.biz
owen@tamarindridgeline.biz

Phone: 604 317 8842
#2714 - 582 E. Halvern St.
Vancouver, B.C. V7K2R4 Canada
Nice to have
• - For the "FRONT" side of our business card. You can separate or re-arrange with our logo components (icon, logo,slogan). It does not have to be together.

Also our company legal name is rather long so arrange or organize the name in a way to make it shorter. Your experience and creativity will have to come in play.
Should not have
• should not have other colors beside logo color and black text (2 colors). Also nothing Three dimensional

```html
<!DOCTYPE html>
<html lang="en">
<head>
<meta charset="utf-8">
<title>Ridgeline Press — Business Card</title>
<link href="https://fonts.googleapis.com/css2?family=Open+Sans:wght@400;600;700&display=swap" rel="stylesheet">
<style>
  :root {
    --brand-blue: #2787cc;
    --brand-blue-deep: #1768aa;
    --ink: #111418;
    --white: #ffffff;
    --silver-light: #f4f5f6;
    --silver-mid: #c9ccd0;
    --page: #e6e7e9;
  }
  * { box-sizing: border-box; margin: 0; padding: 0; }
  html, body {
    width: 1200px; height: 951px; overflow: hidden;
    background: var(--page);
    font-family: "Open Sans", Arial, sans-serif;
  }
  .stage { position: relative; width: 1200px; height: 951px; }

  .card {
    position: absolute; width: 620px; height: 354px;
    border-radius: 22px; overflow: hidden;
  }

  /* Back side: logo lockup */
  .card--back {
    left: 90px; top: 90px;
    background: radial-gradient(ellipse at 45% 40%, var(--brand-blue) 0%, var(--brand-blue-deep) 100%);
    display: flex; flex-direction: column; align-items: center; justify-content: center;
  }
  .brand-mark {
    display: flex; align-items: center; gap: 14px;
    color: var(--white); font-weight: 700; font-size: 40px; letter-spacing: .5px;
    margin-bottom: 26px;
  }
  .brand-mark__dot { width: 22px; height: 22px; border-radius: 50%; background: var(--white); }
  .card--back .site-url {
    color: var(--ink); font-weight: 700; font-size: 37px; line-height: 1; letter-spacing: -.3px;
  }
  .card--back .slogan {
    color: var(--white); font-size: 30px; margin-top: 6px;
  }

  /* Front side: contact details */
  .card--front {
    left: 490px; top: 500px;
    background: linear-gradient(180deg, var(--silver-light) 0%, var(--silver-mid) 100%);
  }
  .front-band { position: absolute; inset: 0; width: 100%; height: 100%; }
  .contact {
    position: absolute; left: 34px; top: 34px; color: var(--white);
  }
  .contact__name { font-size: 25px; font-weight: 600; }
  .contact__title { font-size: 14px; margin-top: 2px; }
  .contact__list { list-style: none; margin-top: 46px; font-size: 15px; line-height: 1.35; }
  .contact__list li { display: flex; gap: 8px; align-items: flex-start; }
  .contact__list li + li { margin-top: 4px; }
  .contact__list .address { margin-bottom: 14px; }
  .contact__list svg { flex: none; width: 14px; height: 14px; margin-top: 3px; fill: var(--white); }

  .front-logo {
    position: absolute; right: 28px; top: 110px; width: 220px;
    display: flex; flex-direction: column; align-items: flex-start;
  }
  .front-logo .brand-mark {
    color: var(--brand-blue); font-size: 26px; gap: 10px; margin-bottom: 16px;
  }
  .front-logo .brand-mark__dot { width: 16px; height: 16px; background: var(--brand-blue); }
  .front-logo .slogan { color: var(--ink); font-size: 17px; }
</style>
</head>
<body>
<main class="stage">

  <section class="card card--back" aria-label="Business card back">
    <div class="brand-mark"><span class="brand-mark__dot"></span>Ridgeline Press</div>
    <p class="site-url">www.tamarindridgeline.biz</p>
    <p class="slogan">Your information gateway</p>
  </section>

  <section class="card card--front" aria-label="Business card front">
    <svg class="front-band" viewBox="0 0 620 354" preserveAspectRatio="none" aria-hidden="true">
      <defs>
        <linearGradient id="bandBlue" x1="0" y1="0" x2="0" y2="1">
          <stop offset="0" stop-color="#2a8ad0"/>
          <stop offset="1" stop-color="#1768aa"/>
        </linearGradient>
      </defs>
      <path d="M0 0 H372 C352 120 352 240 372 354 H0 Z" fill="url(#bandBlue)"/>
    </svg>

    <div class="contact">
      <h1 class="contact__name">Owen Farsk</h1>
      <p class="contact__title">Director of Sales &amp; Marketing</p>
      <ul class="contact__list">
        <li class="address">
          <svg viewBox="0 0 16 16"><path d="M8 1 1 7.5h2V15h4v-4h2v4h4V7.5h2z"/></svg>
          <span>#2714 - 582 E. Halvern St.<br>Vancouver, B.C. V7K2R4 Canada</span>
        </li>
        <li>
          <svg viewBox="0 0 16 16"><path d="M4 1h3l1 4-2 1.5c.8 1.8 2.2 3.2 4 4L11.5 8l4 1v3c0 1.7-1.3 3-3 3C6.5 15 1 9.5 1 3.5 1 2 2.3 1 4 1z"/></svg>
          <span>604 317 8842</span>
        </li>
        <li>
          <svg viewBox="0 0 16 16"><path d="M1 3h14v10H1zM2 4v1l6 4 6-4V4z"/></svg>
          <span>owen@tamarindridgeline.biz</span>
        </li>
        <li>
          <svg viewBox="0 0 16 16"><circle cx="8" cy="8" r="7"/></svg>
          <span>www.tamarindridgeline.biz</span>
        </li>
      </ul>
    </div>

    <div class="front-logo">
      <div class="brand-mark"><span class="brand-mark__dot"></span>Ridgeline Press</div>
      <p class="slogan">Your information gateway</p>
    </div>
  </section>

</main>
</body>
</html>
```